Need CATCHY/VIVID Banner design for my new UTV/ATV/Off Road Vehicle turn signal/lighting company

I need a banner ad designed so I can advertise on several different ATV (all terrain vehicle), UTV (Utility Vehicles), Golf Cart and Off-Road Vehicle forums. Ads need to be very catchy and produce a call to action. Action is getting hits to my website. Our main business is selling turn signal kits to make your side by side or your ATV/UTV street legal, as some states now allow you to drive these on public roads if you have the following items: Turn Signals, Horn, Lighted license plate bracket, headlights and brake lights. We sell all of these items for just about any model vehicle out there. Our call to action for this banner would be to get more website visits.

Target Market(s)

Off-road/outdoor enthusiasts,

Industry/Entity Type

Car Accessorie

Font styles to use
Sans Serif

Requirements
Must have
• Ad size need to be either 728x90 or 300x250. Colorful ad with an off-road vehicle integrated to the design (think UTV, side-by-side, etc.
Nice to have
• Nice to haves would be anything that makes this banner ad stand out on very boring web pages.
Should not have
• anything dull

```html
<!DOCTYPE html>
<html lang="en">
<head>
<meta charset="utf-8">
<title>Trailbright – ATV Signal Lighting Banner</title>
<link rel="stylesheet" href="https://fonts.googleapis.com/css2?family=Roboto:wght@300;400;700;900&display=swap">
<style>
  :root {
    --red: #e5232d;
    --red-orange: #ec4a26;
    --orange: #f37b1f;
    --amber: #f8a41c;
    --deep-orange: #e2521c;
    --white: #ffffff;
    --pale: #f2efe9;
    --sand: #b89878;
    --rock: #8c7158;
    --shadow-brown: #4a3a2d;
  }
  html, body {
    margin: 0;
    padding: 0;
    width: 1200px;
    height: 148px;
    overflow: hidden;
    background: var(--white);
  }
  .banner {
    position: relative;
    width: 1200px;
    height: 148px;
    overflow: hidden;
    font-family: "Roboto", Arial, sans-serif;
    color: var(--white);
    background: linear-gradient(90deg, var(--red) 0%, var(--red-orange) 30%, var(--orange) 55%, var(--amber) 78%, var(--amber) 100%);
  }
  .banner p { white-space: nowrap; }
  .scene-shapes, .trail-photo {
    position: absolute;
    left: 0;
    top: 0;
  }
  .brand {
    position: absolute;
    left: 4px;
    top: 0;
    width: 240px;
    text-align: center;
    text-transform: uppercase;
    font-weight: 900;
  }
  .brand-name {
    margin: 36px 0 0;
    font-size: 30px;
    line-height: 1;
    letter-spacing: 0.5px;
  }
  .brand-tagline {
    margin: 24px 0 0;
    font-size: 23px;
    line-height: 1;
    letter-spacing: -0.4px;
  }
  .brand-subtagline {
    margin: 4px 0 0;
    font-size: 14.5px;
    line-height: 1;
    letter-spacing: 0.4px;
  }
  .vehicle-photo {
    position: absolute;
    left: 252px;
    top: 12px;
    width: 180px;
    height: 136px;
    border-radius: 40% 40% 18% 18%;
    background: radial-gradient(ellipse at 50% 45%, #b7b1a8 0%, #8e8881 40%, #3b3733 75%, rgba(40,36,33,0) 100%);
  }
  .headline {
    position: absolute;
    left: 424px;
    top: 20px;
    width: 320px;
    text-align: center;
    text-transform: uppercase;
  }
  .headline-top {
    margin: 0;
    font-weight: 300;
    font-size: 31px;
    line-height: 32px;
    letter-spacing: 0.3px;
  }
  .headline-main {
    margin: 0;
    font-weight: 700;
    font-size: 32px;
    line-height: 38px;
    letter-spacing: 0.2px;
  }
  .feature-icons {
    position: absolute;
    left: 452px;
    top: 97px;
  }
</style>
</head>
<body>
  <div class="banner">
    <svg class="scene-shapes" width="1200" height="148" viewBox="0 0 1200 148" aria-hidden="true">
      <polygon points="736,0 800,0 830,74 800,148 736,148 766,74" fill="var(--deep-orange)"/>
      <polygon points="786,0 812,0 842,74 812,148 786,148 816,74" fill="var(--pale)"/>
    </svg>

    <svg class="trail-photo" width="1200" height="148" viewBox="0 0 1200 148" role="img" aria-label="Photo of a red off-road side-by-side climbing over desert boulders with hills behind">
      <defs>
        <linearGradient id="trailTones" x1="0" y1="0" x2="1" y2="1">
          <stop offset="0" stop-color="var(--sand)"/>
          <stop offset="0.45" stop-color="var(--rock)"/>
          <stop offset="0.8" stop-color="var(--shadow-brown)"/>
          <stop offset="1" stop-color="#2a2220"/>
        </linearGradient>
      </defs>
      <polygon points="812,0 1200,0 1200,148 812,148 842,74" fill="url(#trailTones)"/>
    </svg>

    <div class="brand">
      <p class="brand-name">Trailbright</p>
      <p class="brand-tagline">Turn Signal Kits</p>
      <p class="brand-subtagline">&amp; Lighting Accessories</p>
    </div>

    <div class="vehicle-photo" role="img" aria-label="Photo of a grey and red sport side-by-side vehicle"></div>

    <div class="headline">
      <p class="headline-top">ATV Vechicle</p>
      <p class="headline-main">Signal Lighting</p>
    </div>

    <svg class="feature-icons" width="264" height="30" viewBox="0 0 264 30" role="img" aria-label="Brake lights, headlights, horn, turn signals, traffic lights">
      <g fill="none" stroke="var(--white)" stroke-width="2.4" stroke-linecap="round" stroke-linejoin="round">
        <circle cx="16" cy="15" r="9"/>
        <path d="M4 6 A13 13 0 0 0 4 24"/>
        <path d="M28 6 A13 13 0 0 1 28 24"/>
        <line x1="16" y1="10" x2="16" y2="16"/>
        <line x1="84" y1="7" x2="92" y2="7"/>
        <line x1="84" y1="12" x2="92" y2="12"/>
        <line x1="84" y1="17" x2="92" y2="17"/>
        <line x1="84" y1="22" x2="92" y2="22"/>
        <path d="M128 12 L142 12 L156 5 L156 25 L142 18 L128 18 Z"/>
        <line x1="132" y1="18" x2="132" y2="24"/>
        <line x1="118" y1="8" x2="122" y2="11"/>
        <line x1="117" y1="15" x2="122" y2="15"/>
        <line x1="118" y1="22" x2="122" y2="19"/>
        <path d="M180 15 L189 6 L189 11 L198 11 L198 19 L189 19 L189 24 Z"/>
        <path d="M226 15 L217 6 L217 11 L208 11 L208 19 L217 19 L217 24 Z"/>
        <rect x="245" y="2" width="12" height="26" rx="3"/>
        <line x1="241" y1="7" x2="245" y2="7"/>
        <line x1="241" y1="14" x2="245" y2="14"/>
        <line x1="257" y1="7" x2="261" y2="7"/>
        <line x1="257" y1="14" x2="261" y2="14"/>
      </g>
      <g fill="var(--white)">
        <circle cx="16" cy="20.5" r="1.5"/>
        <path d="M80 5 C66 5 66 25 80 25 Z"/>
        <circle cx="251" cy="8" r="2.5"/>
        <circle cx="251" cy="15" r="2.5"/>
        <circle cx="251" cy="22" r="2.5"/>
      </g>
    </svg>
  </div>
</body>
</html>
```